Investment Management Firm Power point template

Marrow Holdings is a real estate investment firm focused on buying commercial office and residential property in the UK. We produce powerpoint presentations for our Board of Directors, Investment Committee and also to external investors.

We are looking for a powerpoint design template which we can use for future presentations which provide a professional look and feel.

Our current website: http://www.marrowholdings.example.co.uk/

Target Market(s)

Institution Investors, Board of Directors, Professionals

Industry/Entity Type

Real Estate

Requirements
Must have
• Leverage off the current logo and colour scheme. However, does not have to purely rely on this colour scheme.
• - Title page
• - Content Page
• - Slide where graphs can be incorporated
• - Slide where photos can be incorporated
• - Slide of UK Map which can show where the property portfolio is currently located
• - Other slides incorporating smart art or other designs that can be used for future presentations
Nice to have
• An example of graphics that we would love to have in the powerpoint pack which we can easily edit has been attached

```html
<!DOCTYPE html>
<html lang="en">
<head>
<meta charset="utf-8">
<title>Marrow Holdings – Content Slide</title>
<link rel="stylesheet" href="https://fonts.googleapis.com/css2?family=Titillium+Web:wght@300;400;600;700&display=swap">
<style>
  :root {
    --brand-blue: #1f5a8e;
    --brand-dark: #0f2f4d;
    --band-top: #3c6a8f;
    --band-bottom: #2a5677;
    --footer-blue: #2a6593;
    --paper: #ffffff;
    --paper-soft: #f3f5f8;
    --ink: #1c2733;
    --ink-light: #ffffff;
    --rule: #c9d3dd;
  }
  * { margin: 0; padding: 0; box-sizing: border-box; }
  html, body { width: 1200px; height: 900px; overflow: hidden; background: var(--paper); }
  body { font-family: "Titillium Web", sans-serif; font-weight: 300; color: var(--ink); }

  .slide { position: relative; width: 1200px; height: 900px; overflow: hidden; background: var(--paper); }

  .slide-header { position: absolute; top: 0; left: 0; width: 1200px; height: 93px; background: var(--paper); border-bottom: 1px solid var(--rule); }
  .slide-title { position: absolute; left: 24px; top: 26px; font-size: 33px; font-weight: 600; line-height: 1; color: var(--brand-dark); }
  .slide-title .accent { color: var(--brand-blue); }
  .title-rule { position: absolute; left: 0; top: 68px; width: 258px; height: 3px; background: var(--brand-blue); }

  .brand-mark { position: absolute; right: 36px; top: 14px; display: flex; align-items: center; gap: 12px; }
  .brand-name { font-size: 20px; font-weight: 600; color: var(--brand-blue); }
  .brand-square { width: 54px; height: 54px; background: var(--brand-blue); }

  .hero-band { position: absolute; top: 93px; left: 0; width: 1200px; height: 482px;
    background: linear-gradient(180deg, var(--band-top) 0%, var(--band-bottom) 100%); }

  .lower-field { position: absolute; top: 575px; left: 0; width: 1200px; height: 267px;
    background: linear-gradient(135deg, var(--paper) 0%, var(--paper-soft) 100%); }

  .copy { position: absolute; left: 68px; width: 1090px; font-size: 19.5px; line-height: 33px; }
  .copy p + p { margin-top: 33px; }
  .copy strong { font-weight: 700; }
  .copy-on-band { color: var(--ink-light); }
  .copy-on-band h2 { font-size: 25px; font-weight: 700; line-height: 32px; margin-bottom: 0; }
  .copy-block-one { top: 186px; }
  .copy-block-two { top: 453px; }
  .copy-lower { top: 627px; color: var(--ink); }

  .slide-footer { position: absolute; left: 0; bottom: 0; width: 1200px; height: 58px; background: var(--footer-blue); }
  .copyright { position: absolute; left: 20px; top: 14px; font-size: 20px; color: var(--ink-light); }
</style>
</head>
<body>
<main class="slide">
  <header class="slide-header">
    <h1 class="slide-title"><span class="accent">Slide</span> Title Here</h1>
    <div class="title-rule"></div>
    <div class="brand-mark">
      <span class="brand-name">Marrow Holdings</span>
      <span class="brand-square"></span>
    </div>
  </header>

  <div class="hero-band" role="img" aria-label="Blue-toned photograph of a city river skyline with a bridge and tall tower"></div>

  <section class="copy copy-on-band copy-block-one">
    <h2>Lorem ipsum dolor sit amet</h2>
    <p>Lorem ipsum dolor sit amet, consectetur adipiscing elit, sed do eiusmod tempor incididunt ut labore et dolore magna aliqua. Ut enim ad minim &nbsp;<strong>veniam, quis nostrud exercitation. Lorem ipsum dolor sit amet.</strong></p>
    <p>Consectetur adipiscing elit, sed do eiusmod tempor incididunt ut labore et dolore magna aliqua. Ut enim ad minim veniam, quis nostrud exercitation. Consectetur adipiscing elit,</p>
  </section>
  <section class="copy copy-on-band copy-block-two">
    <p>sed do eiusmod tempor incididunt ut labore et dolore magna aliqua. Ut enim ad minim veniam, quis nostrud exercitation.</p>
  </section>

  <div class="lower-field"></div>
  <section class="copy copy-lower">
    <p>Lorem ipsum dolor sit amet, consectetur adipiscing elit, sed do eiusmod tempor incididunt ut labore et dolore magna aliqua. Ut enim ad minim &nbsp;<strong>veniam, quis nostrud exercitation. Lorem ipsum dolor sit amet.</strong></p>
    <p>Consectetur adipiscing elit, sed do eiusmod tempor incididunt ut labore et dolore magna aliqua. Ut enim ad minim veniam, quis nostrud exercitation. Consectetur adipiscing elit,</p>
  </section>

  <footer class="slide-footer">
    <span class="copyright">Copyright text here</span>
  </footer>
</main>
</body>
</html>
```